Lucivane signs for fridge and desk

I require 3 a4 designs very basic designs with single colour and easy to print. I have atached a style guide to see the fonts I used in my last three design. Please remember I'm printing in only one colour
PLease see the following link, of what I sell on tolvaro. I will be selling this allong side these products.
https://www.tolvaro.com/gp/product/K38N2XRDMV
Please see my competitors
https://www.tolvaro.com/Planner-Magnetic-Calendar-Refrigerator-Container/dp/K9QWRT4HZP/ref=sr_1_8?keywords=acrylic%2Bnote%2Bboard%2Brefrigerator%2Bdry%2Berase%2Bboard%2Bmagnetic%2Bclear&qid=1593816420&sr=8-8&th=1
and
https://www.tolvaro.com/Magnetic-Acrylic-Calendar-Fridge-Refrigerator/dp/K7MXPD2VQS/ref=sr_1_4_sspa?keywords=acrylic+note+board+refrigerator+dry+erase+board+magnetic+clear&qid=1593816377&sr=8-4-spons&psc=1&spLa=QmV0YVZhbHVlT25lVHdvVGhyZWVGb3VyRml2ZVNpeFNldmVuRWlnaHROaW5lVGVuRWxldmVuVHdlbHZlVGhpcnRlZW5Gb3VydGVlbkZpZnRlZW5TaXh0ZWVuU2V2ZW50ZWVuRWlnaHRlZW5OaW5ldGVlblR3ZW50eVR3ZW50eU9uZVR3ZW50eVR3b1R3ZW50eVRocmVlVHdlbnR5Rm91clR3ZW50eUZpdmVUd2VudHlTaXhUd2VudHlTZXZlbg==
I'd like something more fun and different. But that can still be printed on Lucivane with one colour and be functional. A shopping list, a weekly planner(both that stick to a fridge) and a to do list that will sit on a desk or kitchen counter top.
PLease design
1st a4
Break into seven parts, with seven headings..... Monday to Sunday.... here customers will be able to write menus and upcoming events. I want this landcape
2nd a4
'Shopping List' is to be the heading
I want this landcape
3rd a4
'To Do List' is the only text I would like
I would like this portrat and lines marked and a check box on the left hand side
Remember I can only print on the acrylic with one colour. I want to be different from my competitors but I do want to be functional.
just a reminder. I can only print with one colour

```html
<!DOCTYPE html>
<html lang="en">
<head>
<meta charset="utf-8">
<title>Weekly Planner – Fridge Board</title>
<link href="https://fonts.googleapis.com/css2?family=Kaushan+Script&family=Montserrat:wght@500&display=swap" rel="stylesheet">
<style>
  :root {
    --ink: #141414;
    --paper: #ffffff;
    --page: #ffffff;
    --deco: #3a3a3a;
    --rule: #2b2b2b;
  }
  * { box-sizing: border-box; margin: 0; padding: 0; }
  html, body {
    width: 798px;
    height: 1200px;
    overflow: hidden;
    background: var(--page);
  }
  .canvas {
    position: relative;
    width: 798px;
    height: 1200px;
  }
  .planner-board {
    position: absolute;
    left: 83px;
    top: 360px;
    width: 632px;
    height: 439px;
    background: var(--paper);
    border: 2px solid var(--ink);
    border-radius: 11px;
    overflow: hidden;
  }
  .board-header {
    position: relative;
    height: 67px;
    background: var(--ink);
  }
  .header-art {
    position: absolute;
    top: 0;
    height: 67px;
    background: linear-gradient(180deg, var(--deco), #242424);
    border-radius: 0 0 14px 14px;
    opacity: 0.7;
  }
  .header-art--left { left: 14px; width: 158px; }
  .header-art--right { left: 452px; width: 170px; }
  .board-title {
    position: absolute;
    left: 0;
    right: 0;
    top: 8px;
    text-align: center;
    font-family: "Kaushan Script", cursive;
    font-size: 39px;
    line-height: 50px;
    color: var(--paper);
  }
  .day-list { list-style: none; }
  .day-row {
    position: relative;
    height: 52.5px;
    border-bottom: 1.2px solid var(--rule);
    margin: 0 13px 0 12px;
  }
  .day-row:last-child { border-bottom: none; }
  .day-name {
    position: absolute;
    left: 0;
    width: 122px;
    top: 10px;
    text-align: center;
    font-family: "Kaushan Script", cursive;
    font-size: 24px;
    line-height: 30px;
    color: var(--ink);
  }
  .print-note {
    position: absolute;
    left: 0;
    right: 0;
    top: 828px;
    text-align: center;
    font-family: "Montserrat", sans-serif;
    font-weight: 500;
    font-size: 11px;
    letter-spacing: 0.2px;
    color: var(--ink);
  }
</style>
</head>
<body>
<div class="canvas">
  <section class="planner-board">
    <header class="board-header">
      <div class="header-art header-art--left" role="img" aria-label="Line drawings of a tea cup, fried egg, heart and strawberry"></div>
      <h1 class="board-title">Weekly Planner</h1>
      <div class="header-art header-art--right" role="img" aria-label="Line drawings of a croissant, cooking pot and carrot"></div>
    </header>
    <ul class="day-list">
      <li class="day-row"><span class="day-name">Sunday</span></li>
      <li class="day-row"><span class="day-name">Monday</span></li>
      <li class="day-row"><span class="day-name">Tuesday</span></li>
      <li class="day-row"><span class="day-name">Wednesday</span></li>
      <li class="day-row"><span class="day-name">Thursday</span></li>
      <li class="day-row"><span class="day-name">Friday</span></li>
      <li class="day-row"><span class="day-name">Saturday</span></li>
    </ul>
  </section>
  <p class="print-note">THIS WILL BE WHITE COLOUR, , OR ANY COLOUR DEPENDING ON REQUIREMENT</p>
</div>
</body>
</html>
```